GlassHaven Artbook for Okanagan Region, British Columbia

Creating an art book: GlassHaven, for the Okanagan Wine Region in British Columbia, Canada. Would like smart, modern, clean and linear...cool, sexy urban, not ugly boring suburban... I need a cover that appeals to the wino in all of us! Title: GlassHaven -Marla Dovicki
Updates
Thank you all kindly for your efforts. I have added some files so that you can get a sense of my aesthetic...it's never easy trying to figure it out, is it? I will hopefully have dimensions of book soon...cheers, Marla
would anyone please design a giant wine bottle with the wine label that looks like a label but says glasshaven...just curious to see if it works as a design or not...thank you.
Target Market(s)
Designing this wine art book of quotes to wineries in Okanagan BC. Buyer is wine lover and tourist ready to spend his vacation bucks on this wonderful book!
Look and feel

```html
<!DOCTYPE html>
<html lang="en">
<head>
<meta charset="utf-8">
<title>GlassHaven — Marla Dovicki</title>
<link rel="stylesheet" href="https://fonts.googleapis.com/css2?family=Open+Sans:wght@400&family=Questrial&display=swap">
<style>
  :root {
    --paper: #ffffff;
    --blush: #ff7070;
    --rose: #ff4d4d;
    --scarlet: #ff3333;
    --crimson: #d40000;
    --burgundy: #9c0000;
    --title-font: "Open Sans", sans-serif;
    --byline-font: "Questrial", sans-serif;
  }
  html, body {
    margin: 0;
    padding: 0;
    overflow: hidden;
    background: var(--paper);
  }
  .cover {
    position: relative;
    width: 1194px;
    height: 1200px;
    overflow: hidden;
    background: var(--paper);
  }
  .band {
    position: absolute;
    left: 0;
    width: 100%;
  }
  .band--blush    { top: 472px; height: 57px;  background: var(--blush); }
  .band--rose     { top: 529px; height: 89px;  background: var(--rose); }
  .band--scarlet  { top: 618px; height: 149px; background: var(--scarlet); }
  .band--crimson  { top: 767px; height: 178px; background: var(--crimson); }
  .band--burgundy { top: 945px; height: 255px; background: var(--burgundy); }

  .cover-type {
    position: absolute;
    inset: 0;
    width: 1194px;
    height: 1200px;
  }
  .title-first {
    font-family: var(--title-font);
    font-size: 258px;
    letter-spacing: -10px;
    fill: var(--blush);
  }
  .title-second {
    font-family: var(--title-font);
    font-size: 204px;
    letter-spacing: -6px;
    fill: var(--paper);
  }
  .byline {
    font-family: var(--byline-font);
    font-size: 42px;
    letter-spacing: 1px;
    fill: var(--paper);
  }
</style>
</head>
<body>
  <main class="cover">
    <div class="band band--blush"></div>
    <div class="band band--rose"></div>
    <div class="band band--scarlet"></div>
    <div class="band band--crimson"></div>
    <div class="band band--burgundy"></div>

    <svg class="cover-type" viewBox="0 0 1194 1200" xmlns="http://www.w3.org/2000/svg">
      <title>GlassHaven by Marla Dovicki</title>
      <text class="title-first" x="158" y="472">Glass</text>
      <text class="title-second" x="466" y="630">Haven</text>
      <text class="byline" x="1107" y="1140" text-anchor="end">Marla Dovicki</text>
    </svg>
  </main>
</body>
</html>
```